Membership Based Medical Practice Website

We need a functioning website for a new Membership based medical practice. There will be an enrollment fee and a monthly fee. We would like to see designs that are modern, simple. Should use neutral light colors. Examples of sites we like are www.kellanmoorclinic.com and https://fernholtcare.com/ We also have a link that when "Join Now" is clicked it will go to the signup website.

Target Market(s)

Gay Men, local population, Age group 20 to 60's.

Industry/Entity Type

Medical

Coding

Coded - Design and coding required

Number of Pages Required

5+ page

Font styles to use
Sans Serif

Colors
ffffff
cee9f5
ecf7fb
cfeae6
edf8f6
aaaaaa
e9e9e9
dbdbdb
fff3d1

Requirements
Must have
• Logo and header on every page. Clean, simple design, clear content, mobile compatible.
• Must use Wordpress
Nice to have
• Ideas should come from kellanmoorclinic.com
• Easy to read
Should not have
• Generic patient pictures, bold colors.
• Should not copy from above websites.

```html
<!DOCTYPE html>
<html lang="en">
<head>
<meta charset="utf-8">
<title>FAQ – Ashgrove Infectious Disease Specialists</title>
<link href="https://fonts.googleapis.com/css2?family=Lato:wght@300;400;700;900&display=swap" rel="stylesheet">
<style>
  :root {
    --white: #ffffff;
    --ink: #2f2f2f;
    --body-ink: #3a3a3a;
    --muted: #555555;
    --accent-blue: #1a8fcd;
    --faq-bg: #e8f5fa;
    --rule: #c8d2d7;
    --mint: #cfeae6;
    --gold: #c9a65a;
    --icon-grey: #6f6f6f;
  }
  * { box-sizing: border-box; margin: 0; padding: 0; }
  html, body {
    width: 1109px; height: 1200px; overflow: hidden;
    background: var(--white);
    font-family: "Lato", sans-serif;
    color: var(--ink);
  }
  a { text-decoration: none; color: inherit; }
  .page { position: relative; width: 1109px; height: 1200px; }

  /* Header */
  .site-header { position: relative; height: 132px; }
  .brand {
    position: absolute; left: 66px; top: 12px; width: 176px;
    text-align: center; color: var(--muted);
  }
  .brand-mark {
    display: block; width: 64px; height: 64px; margin: 0 auto 14px;
    border: 1.5px solid var(--gold); border-radius: 50%;
  }
  .brand-name {
    display: block; font-size: 13px; font-weight: 400; color: var(--muted);
    letter-spacing: 13px; margin-right: -13px; line-height: 16px;
  }
  .brand-tagline {
    display: block; font-size: 10.5px; font-weight: 400; color: var(--muted);
    letter-spacing: -0.2px; line-height: 14px; white-space: nowrap;
  }
  .main-nav {
    position: absolute; left: 409px; top: 51px; height: 39px;
    display: flex; align-items: center; gap: 39px;
  }
  .main-nav a, .footer-nav a {
    font-size: 13px; font-weight: 700; color: var(--ink);
    text-transform: uppercase; letter-spacing: 0.2px;
  }
  .join-button {
    position: absolute; left: 930px; top: 51px; width: 111px; height: 39px;
    border-radius: 20px; background: var(--mint);
    display: flex; align-items: center; justify-content: center;
    font-size: 14px; font-weight: 700; color: var(--ink); letter-spacing: 0.6px;
  }

  /* Hero */
  .page-hero {
    position: relative; height: 173px;
    background: linear-gradient(180deg, #9a9fa6 0%, #a9aeb1 28%, #76806a 55%, #56604f 80%, #474b44 100%);
    display: flex; align-items: center; justify-content: center;
  }
  .page-hero h1 {
    margin-top: -22px;
    font-size: 38px; font-weight: 900; color: var(--white); letter-spacing: 0.5px;
  }

  /* FAQ */
  .faq-section { height: 735px; background: var(--faq-bg); padding-top: 57px; }
  .faq-title {
    text-align: center; font-size: 31px; font-weight: 400; color: #444;
    line-height: 36px; height: 52px;
  }
  .faq-list { width: 806px; margin: 0 auto; list-style: none; }
  .faq-item { border-bottom: 1px solid var(--rule); }
  .faq-item:last-child { border-bottom: none; }
  .faq-question {
    height: 50px; display: flex; align-items: center; justify-content: space-between;
    font-size: 17px; font-weight: 700; color: var(--accent-blue);
  }
  .faq-item.first .faq-question { height: 62px; }
  .faq-item.open .faq-question { height: 70px; }
  .faq-toggle { width: 14px; height: 14px; flex: none; }
  .faq-answer {
    margin-top: -8px; padding-bottom: 28px; padding-right: 4px;
    font-size: 13.4px; line-height: 24.7px; color: var(--body-ink);
  }

  /* Footer */
  .site-footer { height: 160px; padding-top: 35px; text-align: center; }
  .footer-nav { display: flex; justify-content: center; gap: 39px; height: 20px; align-items: center; }
  .copyright { margin-top: 10px; font-size: 12px; color: var(--ink); }
  .social-links { margin-top: 16px; display: flex; justify-content: center; gap: 16px; }
  .social-dot { width: 18px; height: 18px; border-radius: 50%; background: var(--icon-grey); }
</style>
</head>
<body>
<div class="page">
  <header class="site-header">
    <a class="brand" href="#">
      <span class="brand-mark"></span>
      <span class="brand-name">ASHGROVE</span>
      <span class="brand-tagline">INFECTIOUS DISEASE SPECIALISTS</span>
    </a>
    <nav class="main-nav">
      <a href="#">Home</a>
      <a href="#">Specialties</a>
      <a href="#">Pricing</a>
      <a href="#">About Us</a>
      <a href="#">FAQ</a>
      <a href="#">Blog</a>
    </nav>
    <a class="join-button" href="#">JOIN US</a>
  </header>

  <section class="page-hero" role="img" aria-label="Banner photo of a quiet country road through grassy fields under a misty sky">
    <h1>FAQ</h1>
  </section>

  <section class="faq-section">
    <h2 class="faq-title">FAQ</h2>
    <ul class="faq-list">
      <li class="faq-item first">
        <div class="faq-question">Why do we do things this way?
          <svg class="faq-toggle" viewBox="0 0 14 14"><rect x="5.5" y="0" width="3" height="14" fill="var(--accent-blue)"/><rect x="0" y="5.5" width="14" height="3" fill="var(--accent-blue)"/></svg>
        </div>
      </li>
      <li class="faq-item open">
        <div class="faq-question">Wait, so I can email my doctor?
          <svg class="faq-toggle" viewBox="0 0 14 14"><rect x="0" y="5.5" width="14" height="3" fill="var(--accent-blue)"/></svg>
        </div>
        <p class="faq-answer">Yes!Insurance companies generally reimburse doctors only for time spent face-to-face with patients, and don’t pay doctors for their time spent communicating with patients by phone or email. This is the reason that most doctors require a face-to-face visit (and a copay) any time you have a question, even if the question could have been answered with a quick phone call or email.<br>We do not bill insurance for office visits which allows us to spend more time with our patients. We understand that your time is valuable, and if we can take care of you appropriately without an office visit, we will.</p>
      </li>
      <li class="faq-item">
        <div class="faq-question">Is this concierge medicine?
          <svg class="faq-toggle" viewBox="0 0 14 14"><rect x="5.5" y="0" width="3" height="14" fill="var(--accent-blue)"/><rect x="0" y="5.5" width="14" height="3" fill="var(--accent-blue)"/></svg>
        </div>
      </li>
      <li class="faq-item">
        <div class="faq-question">Do I need insurance?
          <svg class="faq-toggle" viewBox="0 0 14 14"><rect x="5.5" y="0" width="3" height="14" fill="var(--accent-blue)"/><rect x="0" y="5.5" width="14" height="3" fill="var(--accent-blue)"/></svg>
        </div>
      </li>
      <li class="faq-item">
        <div class="faq-question">How can I save on insurance costs as becoming a member?
          <svg class="faq-toggle" viewBox="0 0 14 14"><rect x="5.5" y="0" width="3" height="14" fill="var(--accent-blue)"/><rect x="0" y="5.5" width="14" height="3" fill="var(--accent-blue)"/></svg>
        </div>
      </li>
      <li class="faq-item">
        <div class="faq-question">Can I still use my insurance to pay for labs, imaging, or medications ordered by Dr. Halvorsen?
          <svg class="faq-toggle" viewBox="0 0 14 14"><rect x="5.5" y="0" width="3" height="14" fill="var(--accent-blue)"/><rect x="0" y="5.5" width="14" height="3" fill="var(--accent-blue)"/></svg>
        </div>
      </li>
      <li class="faq-item">
        <div class="faq-question">Can I use my HSA or FSA?
          <svg class="faq-toggle" viewBox="0 0 14 14"><rect x="5.5" y="0" width="3" height="14" fill="var(--accent-blue)"/><rect x="0" y="5.5" width="14" height="3" fill="var(--accent-blue)"/></svg>
        </div>
      </li>
      <li class="faq-item">
        <div class="faq-question">What happens if I'm in the hospital?
          <svg class="faq-toggle" viewBox="0 0 14 14"><rect x="5.5" y="0" width="3" height="14" fill="var(--accent-blue)"/><rect x="0" y="5.5" width="14" height="3" fill="var(--accent-blue)"/></svg>
        </div>
      </li>
    </ul>
  </section>

  <footer class="site-footer">
    <nav class="footer-nav">
      <a href="#">Home</a>
      <a href="#">Specialties</a>
      <a href="#">Pricing</a>
      <a href="#">About Us</a>
      <a href="#">FAQ</a>
      <a href="#">Blog</a>
    </nav>
    <p class="copyright">Copyright © 2019 CompanyName All Rights Reserved.</p>
    <div class="social-links" aria-label="Social media links">
      <span class="social-dot"></span>
      <span class="social-dot"></span>
      <span class="social-dot"></span>
      <span class="social-dot"></span>
      <span class="social-dot"></span>
    </div>
  </footer>
</div>
</body>
</html>
```